Business card design for holistic health care clinic

We need a double-sided business card design for our holistic health care clinic that integrates our logo design and also its color scheme. My business is called Valmira. It is an integrative medicine clinic. You have already done the logo for me. Please ensure an elegant and upscale design that is not cluttered, but still has all the necessary information (please see below for details).

Target Market(s)

Wellness, fitness, rehabilitation for educated, well-traveled open-minded clients who are focused on natural, organic, balanced and preventive healthcare and lifestyle.

Industry/Entity Type

Medical

Contact Information for Business Card

Modern, clean.

Number of Pages Required

1 page

Font styles to use
Serif
Sans Serif

Colors

Designer to choose colors to be used in the design.

Requirements
Must have
• Logo on one side, all other information on the other side.
• Other information should include:
• Tobias Wrenfeld - DOE, CPT, LMT
• 4100 East Marrow Drive
• Austin, TX 78119
• 512 555 0148
• 818 555 0192
• info@ValmiraHealth.example
• t.wrenfeld@ValmiraHealth.example
Nice to have
• Darker background on front - but not totally black - shaded/dark gray.

```html
<!DOCTYPE html>
<html lang="en">
<head>
<meta charset="utf-8">
<title>Valmira – Business Card</title>
<link rel="stylesheet" href="https://fonts.googleapis.com/css2?family=Roboto:wght@400;500&family=Montserrat:wght@500;700&display=swap">
<style>
  :root {
    --card-dark: #2b2b2d;
    --card-white: #ffffff;
    --brand-blue: #1b8fd4;
    --text-light: #f2f2f2;
    --stage: #e9e6e1;
  }
  * { box-sizing: border-box; margin: 0; padding: 0; }
  html, body { width: 1200px; height: 911px; overflow: hidden; }
  body {
    background: var(--stage);
    display: flex;
    align-items: center;
    justify-content: center;
    gap: 120px;
    font-family: "Roboto", Arial, sans-serif;
  }
  .card {
    position: relative;
    width: 360px;
    height: 620px;
    border-radius: 22px;
    background: var(--card-dark);
    overflow: hidden;
    box-shadow: 0 10px 30px rgba(0,0,0,.25);
  }

  /* Contact side */
  .contact-list {
    position: absolute;
    top: 54px;
    left: 0;
    right: 0;
    text-align: center;
    color: var(--text-light);
    font-size: 15px;
    line-height: 1.35;
  }
  .contact-icon { display: block; margin: 0 auto 6px; width: 16px; height: 16px; fill: var(--brand-blue); }
  .contact-name {
    color: var(--brand-blue);
    font-size: 19px;
    font-weight: 500;
    letter-spacing: .5px;
    text-transform: uppercase;
  }
  .contact-credentials { font-size: 11px; text-transform: none; letter-spacing: .3px; }
  .contact-group { margin-bottom: 12px; }
  .contact-group:first-child { margin-bottom: 14px; }

  .wave-area { position: absolute; left: 0; bottom: 0; width: 360px; height: 260px; }
  .wave-name {
    position: absolute;
    left: 0; right: 0; bottom: 78px;
    text-align: center;
    font-family: "Montserrat", Arial, sans-serif;
    font-weight: 700;
    font-size: 40px;
    letter-spacing: 2px;
    color: var(--brand-blue);
  }

  /* Brand side */
  .brand-block {
    position: absolute;
    top: 262px;
    left: 0; right: 0;
    text-align: center;
    color: var(--brand-blue);
    font-family: "Montserrat", Arial, sans-serif;
  }
  .brand-name { font-size: 62px; font-weight: 700; letter-spacing: 2px; line-height: 1; }
  .brand-descriptor { font-size: 17px; font-weight: 500; margin-top: 8px; letter-spacing: .4px; }
  .tagline-band {
    position: absolute;
    left: 0; right: 0;
    bottom: 48px;
    height: 66px;
    background: var(--brand-blue);
    border-top: 10px solid var(--brand-blue);
    box-shadow: inset 0 10px 0 var(--card-dark);
    display: flex;
    align-items: center;
    justify-content: center;
    padding-top: 10px;
    color: var(--text-light);
    font-size: 17px;
  }
  .tagline-band::before {
    content: "";
    position: absolute;
    left: 0; right: 0; top: 6px;
    height: 5px;
    background: var(--brand-blue);
  }
</style>
</head>
<body>

<section class="card card--contact" aria-label="Contact side">
  <div class="contact-list">
    <div class="contact-group">
      <svg class="contact-icon" viewBox="0 0 16 16" aria-hidden="true"><circle cx="8" cy="5" r="3.5"/><path d="M1.5 16c0-4 3-6 6.5-6s6.5 2 6.5 6z"/></svg>
      <div class="contact-name">Tobias Wrenfeld <span class="contact-credentials">- DOE, CPT, LMT</span></div>
    </div>
    <div class="contact-group">
      <svg class="contact-icon" viewBox="0 0 16 16" aria-hidden="true"><path d="M8 0a5.5 5.5 0 0 0-5.5 5.5C2.5 10 8 16 8 16s5.5-6 5.5-10.5A5.5 5.5 0 0 0 8 0zm0 8a2.5 2.5 0 1 1 0-5 2.5 2.5 0 0 1 0 5z"/></svg>
      <div>4100 East Marrow Drive</div>
      <div>Austin, TX 78119</div>
    </div>
    <div class="contact-group">
      <svg class="contact-icon" viewBox="0 0 16 16" aria-hidden="true"><path d="M3.5 1l3 3-1.8 1.8a9 9 0 0 0 5.5 5.5L12 9.5l3 3-2 2.5C6.5 14.5 1.5 9.5 1 3z"/></svg>
      <div>512 555 0148</div>
    </div>
    <div class="contact-group">
      <svg class="contact-icon" viewBox="0 0 16 16" aria-hidden="true"><path d="M4 0h8a1 1 0 0 1 1 1v14a1 1 0 0 1-1 1H4a1 1 0 0 1-1-1V1a1 1 0 0 1 1-1zm.8 2v10.5h6.4V2zM8 13.3a.9.9 0 1 0 0 1.8.9.9 0 0 0 0-1.8z"/></svg>
      <div>818 555 0192</div>
    </div>
    <div class="contact-group">
      <svg class="contact-icon" viewBox="0 0 16 16" aria-hidden="true"><path d="M0 3h16v10H0zm1.5 1.3v.4L8 9l6.5-4.3v-.4z"/></svg>
      <div>t.wrenfeld@ValmiraHealth.example</div>
    </div>
    <div class="contact-group">
      <svg class="contact-icon" viewBox="0 0 16 16" aria-hidden="true"><circle cx="8" cy="8" r="7.5"/><path d="M.5 8h15M8 .5c-4 4-4 11 0 15M8 .5c4 4 4 11 0 15" stroke="#2b2b2d" stroke-width="1.2" fill="none"/></svg>
      <div>www.ValmiraHealth.example</div>
    </div>
  </div>

  <svg class="wave-area" viewBox="0 0 360 260" aria-hidden="true">
    <path d="M0 8 C40 0 70 60 140 80 C220 102 300 90 360 130 L360 260 L0 260 Z" fill="#1b8fd4"/>
    <path d="M0 20 C40 14 70 76 140 96 C220 118 300 106 360 146 L360 260 L0 260 Z" fill="#ffffff"/>
  </svg>
  <div class="wave-name">Valmira</div>
</section>

<section class="card card--brand" aria-label="Brand side">
  <div class="brand-block">
    <div class="brand-name">VALMIRA</div>
    <div class="brand-descriptor">Integrative Holistic Medicine</div>
  </div>
  <div class="tagline-band">helping the body help itself</div>
</section>

</body>
</html>
```